Dalvick's Business Card

I need some designs for a new business card including the new logo attached. An old example of our business card is also attached to show all the data that should be included on the new design.
**I added some more examples someone had mocked up**

Contact Information for Business Card

Should include all info on other examples uploaded.

```html
<!DOCTYPE html>
<html lang="en">
<head>
<meta charset="utf-8">
<title>Dalvick's Business Card</title>
<link href="https://fonts.googleapis.com/css2?family=Montserrat:wght@500;600;700;800&family=Open+Sans:wght@400;600&display=swap" rel="stylesheet">
<style>
  :root {
    --bg: #3b3b3d;
    --card: #141416;
    --blue: #1f74c9;
    --red: #e0302b;
    --white: #f2f2f2;
    --gloss: #2a2a2c;
    --gloss-hi: #55565a;
  }
  * { margin: 0; padding: 0; box-sizing: border-box; }
  html, body { width: 1200px; height: 801px; overflow: hidden; }
  body {
    background: var(--bg);
    font-family: "Open Sans", sans-serif;
    color: var(--white);
    position: relative;
  }
  .card {
    position: absolute;
    top: 252px;
    width: 520px;
    height: 297px;
    background: var(--card);
    border-bottom: 4px solid var(--blue);
    box-shadow: 0 14px 30px rgba(0,0,0,0.45);
    overflow: hidden;
  }
  .card--front { left: 45px; }
  .card--back { left: 635px; }

  /* Front */
  .brand {
    position: absolute;
    left: 46px;
    top: 70px;
    display: flex;
    align-items: center;
    gap: 12px;
  }
  .brand__dot {
    width: 30px; height: 30px;
    border-radius: 50%;
    background: var(--blue);
  }
  .brand__name {
    font-family: "Montserrat", sans-serif;
    font-weight: 800;
    font-size: 44px;
    letter-spacing: 1px;
    color: var(--blue);
    text-transform: uppercase;
  }
  .owner {
    position: absolute;
    left: 46px;
    top: 152px;
    font-family: "Montserrat", sans-serif;
    font-weight: 700;
    font-size: 19px;
    letter-spacing: 0.5px;
    color: var(--blue);
    white-space: nowrap;
  }
  .divider {
    position: absolute;
    left: 280px;
    top: 140px;
    width: 2px;
    height: 50px;
    background: var(--blue);
  }
  .contact {
    position: absolute;
    left: 294px;
    top: 140px;
    list-style: none;
    font-size: 14px;
    line-height: 25px;
    white-space: nowrap;
  }
  .contact li { display: flex; align-items: center; gap: 7px; }
  .contact svg { width: 11px; height: 11px; fill: var(--red); flex: none; }
  .credentials {
    position: absolute;
    left: 46px;
    right: 30px;
    bottom: 36px;
    font-weight: 600;
    font-size: 16px;
    letter-spacing: 0.4px;
    text-transform: uppercase;
    white-space: nowrap;
  }
  .credentials .sep { color: var(--red); margin: 0 8px; }

  /* Back */
  .brand--gloss {
    left: 60px;
    top: 60px;
  }
  .brand--gloss .brand__dot { background: var(--gloss); width: 38px; height: 38px; }
  .brand--gloss .brand__name {
    font-size: 58px;
    color: var(--gloss-hi);
  }
  .service-area {
    position: absolute;
    left: 0; right: 0;
    top: 188px;
    text-align: center;
    font-size: 17px;
    white-space: nowrap;
  }
  .call-to-action {
    position: absolute;
    left: 0; right: 0;
    top: 220px;
    text-align: center;
    font-weight: 600;
    font-size: 12.5px;
    letter-spacing: 0.1px;
    text-transform: uppercase;
    white-space: nowrap;
  }
</style>
</head>
<body>
  <section class="card card--front">
    <div class="brand">
      <span class="brand__dot"></span>
      <span class="brand__name">Dalvick's</span>
    </div>
    <p class="owner">BRENNAN DALVICK</p>
    <span class="divider"></span>
    <ul class="contact">
      <li>
        <svg viewBox="0 0 24 24" aria-hidden="true"><path d="M6.6 10.8a15.1 15.1 0 0 0 6.6 6.6l2.2-2.2c.3-.3.7-.4 1-.2 1.1.4 2.3.6 3.6.6.6 0 1 .4 1 1V20c0 .6-.4 1-1 1A17 17 0 0 1 3 4c0-.6.4-1 1-1h3.5c.6 0 1 .4 1 1 0 1.3.2 2.5.6 3.6.1.3 0 .7-.2 1z"/></svg>
        555.014.2287
      </li>
      <li>
        <svg viewBox="0 0 24 24" aria-hidden="true"><path d="M2 5h20v14H2z M2 5l10 8 10-8" fill="var(--red)" stroke="var(--card)" stroke-width="1.5"/></svg>
        hvacdalvick@mailbox.com
      </li>
    </ul>
    <p class="credentials">Licensed &amp; Insured<span class="sep">•</span>Family Owned &amp; Operated</p>
  </section>

  <section class="card card--back">
    <div class="brand brand--gloss">
      <span class="brand__dot"></span>
      <span class="brand__name">Dalvick's</span>
    </div>
    <p class="service-area">Serves Ridgefield, IA &amp; Surrounding Areas</p>
    <p class="call-to-action">Call today for all your HVAC, refrigeration &amp; plumbing needs</p>
  </section>
</body>
</html>
```